kelvaro stationary business card and letterhead

THIS PROJECT IS TO DESIGN A BUSINESS CARD DOUBLE SIDES .

Reason: I AM WAITING FOR TESINU SUBMISION

Industry/Entity Type

Business

Font styles to use
Other font styles liked:
• Chose your font

```html
<!DOCTYPE html>
<html lang="en">
<head>
<meta charset="utf-8">
<title>Kelvaro Stationery</title>
<link rel="stylesheet" href="https://fonts.googleapis.com/css2?family=Open+Sans:wght@400;600&display=swap">
<style>
  :root {
    --backdrop: #e9e9e9;
    --paper: #f4f4f4;
    --paper-panel: #fafafa;
    --ink: #2d2d2d;
    --ink-soft: #5a5a5a;
    --ink-muted: #8a8a8a;
    --accent: #e6ad1c;
    --band: #2a2a2a;
  }
  * { box-sizing: border-box; margin: 0; padding: 0; }
  html, body { width: 1200px; height: 1000px; overflow: hidden; }
  body {
    background: var(--backdrop);
    font-family: "Open Sans", Arial, sans-serif;
    color: var(--ink);
    position: relative;
  }
  .sheet {
    position: absolute;
    background: var(--paper);
    box-shadow: 0 6px 18px rgba(0,0,0,.12);
  }
  /* brand block: name set as plain text, descriptor in muted grey */
  .brand { display: flex; flex-direction: column; }
  .brand-name { font-weight: 600; color: var(--ink); letter-spacing: .06em; line-height: 1; }
  .brand-tag { font-weight: 400; color: var(--ink-muted); letter-spacing: .04em; }

  /* letterhead */
  .letterhead { left: 520px; top: 40px; width: 640px; height: 920px; }
  .letterhead .brand { position: absolute; right: 56px; top: 64px; align-items: flex-end; }
  .letterhead .brand-name { font-size: 28px; }
  .letterhead .brand-tag { font-size: 10px; margin-top: 6px; }
  .letter-body {
    position: absolute; left: 56px; right: 56px; top: 150px;
    font-size: 10.5px; line-height: 1.6; color: var(--ink-soft);
  }
  .letter-body p { margin-bottom: 14px; }
  .signature {
    width: 150px; height: 46px; margin-top: 20px;
    background: linear-gradient(90deg, #e7e7e7, #ededed);
  }
  .signer { font-size: 11px; color: var(--ink); margin-top: 6px; }
  .letter-footer {
    position: absolute; left: 56px; right: 56px; bottom: 30px;
    display: flex; flex-wrap: nowrap; justify-content: space-between;
    font-size: 8.5px; color: var(--ink-soft); white-space: nowrap;
  }
  .contact-item { display: flex; align-items: center; gap: 4px; }
  .contact-item svg { width: 9px; height: 9px; flex: none; }
  .letter-band { position: absolute; left: 0; right: 0; bottom: 0; height: 16px; background: var(--band); }

  /* cards */
  .card { width: 380px; height: 218px; }
  .card-front { left: 70px; top: 210px; display: flex; align-items: center; justify-content: center; }
  .card-front .brand { align-items: center; }
  .card-front .brand-name { font-size: 32px; }
  .card-front .brand-tag { font-size: 11px; margin-top: 8px; }

  .card-back { left: 70px; top: 560px; overflow: hidden; }
  .card-back .band { position: absolute; left: 0; top: 0; width: 100%; height: 14px; background: var(--band); }
  .card-back .brand { position: absolute; left: 26px; top: 58px; }
  .card-back .brand-name { font-size: 19px; }
  .card-back .brand-tag { font-size: 7.5px; margin-top: 5px; }
  .card-panel {
    position: absolute; right: 0; top: 14px; bottom: 0; width: 168px;
    background: var(--paper-panel); padding: 44px 16px 0 18px;
  }
  .person-name { font-size: 17px; color: var(--ink); }
  .person-role { font-size: 9px; color: var(--accent); margin-bottom: 10px; }
  .card-contacts { font-size: 8px; color: var(--ink-soft); line-height: 1.7; list-style: none; }
  .card-contacts li { display: flex; align-items: center; gap: 5px; white-space: nowrap; }
  .card-contacts svg { width: 7px; height: 7px; flex: none; }
</style>
</head>
<body>

<section class="sheet letterhead">
  <div class="brand">
    <span class="brand-name">KELVARO</span>
    <span class="brand-tag">International Consulting</span>
  </div>

  <div class="letter-body">
    <p>Dear Client</p>
    <p>Lorem ipsum dolor sit amet, consectetur adipiscing elit. Nulla sodales nisi vitae lorem ipsum dolor sit amet, consectetur adipiscing elit. Suspendisse feugiat eros nisl, a facilisis risus eleifend sed. Aliquam mauris enim, fermentum eu lacinia sit amet, laoreet eu leo. Nullam eleifend nulla in libero tristique, ac vulputate odio tincidunt. Etiam non condimentum tortor. Integer suscipit neque nec odio porttitor cursus. Phasellus a sapien blandit, suscipit justo ut, commodo tortor. Morbi tristique justo risus, id mattis dui molestie id. Nullam volutpat ut quam commodo facilisis. Pellentesque urna est, interdum in elit quis, pharetra elementum orci. Nam pharetra velit molestie justo placerat scelerisque.</p>
    <p>Nullam aliquam ligula ac sem aliquet varius. Nullam sed laoreet sapien. Fusce ultricies lobortis odio, sed imperdiet magna lacinia eget. Morbi vitae varius nisl. Phasellus purus felis, congue id tempor quis, porttitor ut sem. Integer luctus nunc posuere at quam interdum, interdum pharetra lectus. Fusce commodo sapien vel consequat tincidunt. Proin sed mi dignissim, accumsan dui ut, luctus turpis. Praesent vulputate elementum nibh. Ut volutpat felis ut mi tincidunt, vitae accumsan quam porta. Sed malesuada bibendum lectus tempor ullamcorper. Nullam interdum diam velit, id porta elit congue quis.</p>
    <p>Pellentesque habitant morbi tristique senectus et netus et malesuada fames ac turpis egestas. Donec quis fermentum massa. Vivamus auctor tincidunt tellus, vel iaculis elit sagittis sit amet. Morbi aliquam pharetra lobortis. Mauris non iaculis ipsum. Morbi tortor ipsum, suscipit a laoreet sed, tempus non risus. Maecenas rhoncus vehicula est, sagittis vulputate magna ullamcorper non. Sed dignissim sapien sed rhoncus imperdiet.</p>
    <p>Best regards,</p>
    <div class="signature" role="img" aria-label="Handwritten signature of Elin Marsh"></div>
    <p class="signer">Elin Marsh</p>
  </div>

  <div class="letter-footer">
    <span class="contact-item">
      <svg viewBox="0 0 10 10"><path d="M5 0.5a3.2 3.2 0 0 0-3.2 3.2C1.8 6 5 9.5 5 9.5S8.2 6 8.2 3.7A3.2 3.2 0 0 0 5 .5zm0 4.4a1.2 1.2 0 1 1 0-2.4 1.2 1.2 0 0 1 0 2.4z" fill="var(--accent)"/></svg>
      48 Harbor Lane, Westvale
    </span>
    <span class="contact-item">
      <svg viewBox="0 0 10 10"><path d="M2.2 1l1.6 1.9-.9 1.2a6 6 0 0 0 3 3l1.2-.9L9 7.8 8.1 9C4.3 9 1 5.7 1 1.9z" fill="var(--accent)"/></svg>
      555-0192-88
    </span>
    <span class="contact-item">
      <svg viewBox="0 0 10 10"><rect x="1" y="2.5" width="8" height="5" fill="var(--accent)"/></svg>
      555-0192-89
    </span>
    <span class="contact-item">
      <svg viewBox="0 0 10 10"><rect x="1" y="2" width="8" height="6" fill="var(--accent)"/><path d="M1 2l4 3.2L9 2" stroke="#fff" stroke-width=".8" fill="none"/></svg>
      hello@kelvaro.example
    </span>
    <span class="contact-item">
      <svg viewBox="0 0 10 10"><circle cx="5" cy="5" r="4" fill="var(--accent)"/></svg>
      www.kelvaro.example
    </span>
  </div>
  <div class="letter-band"></div>
</section>

<section class="sheet card card-front">
  <div class="brand">
    <span class="brand-name">KELVARO</span>
    <span class="brand-tag">International Consulting</span>
  </div>
</section>

<section class="sheet card card-back">
  <div class="band"></div>
  <div class="brand">
    <span class="brand-name">KELVARO</span>
    <span class="brand-tag">International Consulting</span>
  </div>
  <div class="card-panel">
    <p class="person-name">Elin Marsh</p>
    <p class="person-role">Managing Director</p>
    <ul class="card-contacts">
      <li><svg viewBox="0 0 10 10"><circle cx="5" cy="5" r="4" fill="var(--accent)"/></svg>48 Harbor Lane, Westvale</li>
      <li><svg viewBox="0 0 10 10"><circle cx="5" cy="5" r="4" fill="var(--accent)"/></svg>555-0192-88</li>
      <li><svg viewBox="0 0 10 10"><circle cx="5" cy="5" r="4" fill="var(--accent)"/></svg>555-0192-89</li>
      <li><svg viewBox="0 0 10 10"><circle cx="5" cy="5" r="4" fill="var(--accent)"/></svg>hello@kelvaro.example</li>
      <li><svg viewBox="0 0 10 10"><circle cx="5" cy="5" r="4" fill="var(--accent)"/></svg>www.kelvaro.example</li>
    </ul>
  </div>
</section>

</body>
</html>
```